KRV Business Card

Looking for a business card for my restaurant group I own. Four different concepts:

Copperfield Alehouse
Bristow Alehouse
Tanager's Stone Hearth Kitchen
Pellston Patty Company

Card doesn't need to include all the logos.

```html
<!DOCTYPE html>
<html lang="en">
<head>
<meta charset="utf-8">
<title>KRV Business Card</title>
<link href="https://fonts.googleapis.com/css2?family=Lato:wght@400;700&family=Montserrat:wght@500;600&display=swap" rel="stylesheet">
<style>
  :root {
    --backdrop: #7a5a3a;
    --card: #ffffff;
    --gold: #d3ad6a;
    --slate: #6f7073;
    --ink: #5a5b5e;
    --rule: #8a8a8a;
    --ghost: #f4f2ef;
  }
  * { box-sizing: border-box; margin: 0; padding: 0; }
  html, body { width: 900px; height: 1200px; overflow: hidden; }
  body {
    background: var(--backdrop);
    position: relative;
    font-family: "Lato", Arial, sans-serif;
  }
  .card {
    position: absolute;
    background: var(--card);
    border-radius: 24px;
    overflow: hidden;
    box-shadow: 0 6px 14px rgba(0,0,0,0.35);
  }
  .card--front { left: 87px; top: 137px; width: 733px; height: 426px; border-bottom: 4px solid var(--gold); }
  .card--back { left: 87px; top: 632px; width: 735px; height: 430px; }

  .wordmark {
    font-family: "Montserrat", Arial, sans-serif;
    font-weight: 500;
    color: var(--gold);
    position: absolute;
    letter-spacing: 0.08em;
    line-height: 1.15;
  }
  .wordmark__initials { display: block; }
  .card--front .wordmark { left: 26px; top: 24px; }
  .card--front .wordmark__initials { font-size: 46px; }
  .card--front .wordmark__name { display: block; font-size: 30px; margin-top: 6px; }
  .card--front .wordmark__sub { display: block; font-size: 16px; letter-spacing: 0.12em; }

  .ghost-initials {
    position: absolute;
    right: 26px; top: 86px;
    font-family: "Montserrat", Arial, sans-serif;
    font-weight: 600;
    font-size: 150px;
    line-height: 1;
    color: var(--ghost);
    letter-spacing: 0.02em;
  }

  .person-name {
    position: absolute; left: 26px; top: 266px;
    font-family: "Montserrat", Arial, sans-serif;
    font-weight: 600; font-size: 25px;
    color: var(--gold); letter-spacing: 0.02em;
  }
  .divider {
    position: absolute; left: 271px; top: 292px; width: 436px;
    border-top: 1px solid var(--rule);
  }
  .role { position: absolute; left: 477px; top: 265px; font-size: 17px; color: var(--ink); letter-spacing: 0.03em; }
  .venues {
    position: absolute; left: 477px; top: 301px;
    list-style: none; font-size: 17px; color: var(--ink);
    line-height: 28px; letter-spacing: 0.03em;
  }
  .contacts {
    position: absolute; left: 26px; top: 326px;
    list-style: none; font-size: 17px; color: var(--ink); letter-spacing: 0.03em;
  }
  .contacts li { display: flex; align-items: center; height: 28px; }
  .contacts svg { width: 16px; height: 16px; margin-right: 14px; fill: var(--gold); }

  .card--back .wordmark { left: 0; right: 0; top: 92px; text-align: center; }
  .card--back .wordmark__initials { font-size: 82px; }
  .card--back .wordmark__name { display: block; font-size: 50px; margin-top: 4px; }
  .card--back .wordmark__sub { display: block; font-size: 24px; letter-spacing: 0.12em; }
  .web-band {
    position: absolute; left: 0; bottom: 0; width: 100%; height: 64px;
    background: var(--slate);
    display: flex; align-items: center; justify-content: center;
    font-weight: 700; font-size: 17px; color: #fff;
  }
  .web-band span { color: var(--gold); }
</style>
</head>
<body>
  <section class="card card--front">
    <div class="wordmark">
      <span class="wordmark__initials">KRV</span>
      <span class="wordmark__name">KENROW</span>
      <span class="wordmark__sub">HOSPITALITY GROUP</span>
    </div>
    <div class="ghost-initials" aria-hidden="true">KRV</div>

    <h1 class="person-name">MARCUS DELANEY</h1>
    <div class="divider"></div>
    <p class="role">Owner</p>
    <ul class="venues">
      <li>Copperfield Alehouse</li>
      <li>Bristow Alehouse</li>
      <li>Tanager's Stone Hearth Kitchen</li>
      <li>Pellston Patty Company</li>
    </ul>

    <ul class="contacts">
      <li><svg viewBox="0 0 24 24"><path d="M6.6 10.8a15.1 15.1 0 0 0 6.6 6.6l2.2-2.2c.3-.3.7-.4 1-.2 1.1.4 2.3.6 3.6.6.6 0 1 .4 1 1V20c0 .6-.4 1-1 1A17 17 0 0 1 3 4c0-.6.4-1 1-1h3.5c.6 0 1 .4 1 1 0 1.3.2 2.5.6 3.6.1.3 0 .7-.2 1z"/></svg>555.201.4837</li>
      <li><svg viewBox="0 0 24 24"><path d="M2 5h20v14H2z M2 5l10 8 10-8" fill="none" stroke="#d3ad6a" stroke-width="2"/></svg>mdelaney@kenrowmail.com</li>
      <li><svg viewBox="0 0 24 24"><g fill="none" stroke="#d3ad6a" stroke-width="1.8"><circle cx="12" cy="12" r="9.5"/><ellipse cx="12" cy="12" rx="4" ry="9.5"/><path d="M2.5 12h19M4 7h16M4 17h16"/></g></svg>www.kenrowhospitalitygroup.com</li>
    </ul>
  </section>

  <section class="card card--back">
    <div class="wordmark">
      <span class="wordmark__initials">KRV</span>
      <span class="wordmark__name">KENROW</span>
      <span class="wordmark__sub">HOSPITALITY GROUP</span>
    </div>
    <div class="web-band">www.<span>kenrowhospitalitygroup</span>.com</div>
  </section>
</body>
</html>
```